Tech Savy small Business accountant business card design

We need a business card for a new company based in the cloud. We provide tax, business advisory, accounting, information technology solutions and back office functions to small businesses. We offer fixed fee packages with add on services as you need them. By harnessing technology we simplify small business operational processes providing valuable time and information for small business owners to grow their business. In the logo (bluvoria) we want to be able to see bluv and experts. The final design should communicate achieving growth dreams and balance (ie life and $).
Updates
This project has been temporarily placed on hold until I finalize "Tech Savy small Business accountant needs a logo". I invite all designers to submit on this logo project. Once my logo is finalized I will resume this business card contest. Thanks Added Wednesday, March 19, 2014
This project has been temporarily placed on hold until I finalize "Tech Savy small Business accountant logo". I invite all designers to submit on this logo project. Once my logo is finalized I will resume this business card contest. Thanks Added Thursday, March 20, 2014
Target Market(s)
Small Business (Revenue $500,000, more than 3 employees) owners.
Industry/Entity Type
Small Business
Contact Information for Business Card
Marcy Elwind (Principal)
Accountant, Tax Agent.
TEL | 0417 683 912
EMAIL | Marcy.Elwind@bluvoria.com.au
WEB | www.bluvoria.com.au
Look and feel

```html
<!DOCTYPE html>
<html lang="en">
<head>
<meta charset="utf-8">
<title>bluvoria business card</title>
<link rel="stylesheet" href="https://fonts.googleapis.com/css2?family=Questrial&family=Fira+Sans:wght@400&display=swap">
<style>
  :root {
    --blue: #1f96d4;
    --grey: #727176;
    --text-grey: #6b6a6e;
    --white: #ffffff;
    --backdrop: #eeeeee;
  }
  * { margin: 0; padding: 0; box-sizing: border-box; }
  html, body { width: 1189px; height: 1200px; overflow: hidden; background: var(--backdrop); }
  .canvas { position: relative; width: 1189px; height: 1200px; }

  .card {
    position: absolute;
    left: 171px;
    width: 856px;
    height: 486px;
    background: var(--white);
    border-radius: 18px;
    overflow: hidden;
  }
  .card--front { top: 69px; }
  .card--back { top: 627px; }

  .card__bands { position: absolute; inset: 0; width: 100%; height: 100%; }

  .brand-name {
    position: absolute;
    font-family: "Questrial", sans-serif;
    font-weight: 400;
    color: var(--blue);
    line-height: 1;
    white-space: nowrap;
  }
  .tagline {
    position: absolute;
    font-family: "Fira Sans", sans-serif;
    font-weight: 400;
    color: var(--text-grey);
    line-height: 1;
    white-space: nowrap;
  }

  .card--front .brand-name { left: 0; right: 0; text-align: center; top: 150px; font-size: 118px; letter-spacing: -2px; }
  .card--front .tagline { left: 0; right: 0; text-align: center; top: 284px; font-size: 30px; }

  .card--back .brand-name { left: 48px; top: 56px; font-size: 78px; letter-spacing: -1px; }
  .card--back .tagline { left: 50px; top: 148px; font-size: 20px; }

  .person {
    position: absolute;
    right: 47px;
    top: 66px;
    text-align: right;
    font-family: "Questrial", sans-serif;
    line-height: 1;
  }
  .person__name { font-size: 39px; color: var(--blue); }
  .person__role { font-size: 22px; color: var(--text-grey); margin-top: 5px; }
  .person__title { font-size: 24px; color: var(--text-grey); margin-top: 8px; }

  .contacts {
    position: absolute;
    right: 46px;
    top: 218px;
    list-style: none;
    font-family: "Questrial", sans-serif;
    font-size: 23px;
    color: var(--text-grey);
  }
  .contacts__item {
    display: flex;
    justify-content: flex-end;
    align-items: center;
    gap: 12px;
    height: 30px;
    line-height: 1;
  }
  .contacts__icon { width: 24px; height: 24px; flex: none; }

  .location {
    position: absolute;
    right: 43px;
    top: 420px;
    font-family: "Questrial", sans-serif;
    font-size: 24px;
    color: var(--white);
    line-height: 1;
  }
</style>
</head>
<body>
<main class="canvas">

  <section class="card card--front" aria-label="Card front">
    <svg class="card__bands" viewBox="0 0 1048 596" preserveAspectRatio="none" aria-hidden="true">
      <path d="M0,0 H1048 V72 Q600,148 0,132 Z" fill="var(--grey)"/>
      <path d="M75,153 Q620,168 1048,92 V166 Q640,205 75,153 Z" fill="var(--blue)"/>
      <path d="M0,446 Q520,398 985,440 Q520,444 0,516 Z" fill="var(--blue)"/>
      <path d="M0,540 Q480,455 1048,462 V596 H0 Z" fill="var(--grey)"/>
    </svg>
    <h1 class="brand-name">bluvoria</h1>
    <p class="tagline">Your business and accounting partner</p>
  </section>

  <section class="card card--back" aria-label="Card back">
    <svg class="card__bands" viewBox="0 0 1048 596" preserveAspectRatio="none" aria-hidden="true">
      <path d="M0,448 Q520,400 985,442 Q520,446 0,522 Z" fill="var(--blue)"/>
      <path d="M0,542 Q480,458 1048,464 V596 H0 Z" fill="var(--grey)"/>
    </svg>
    <h2 class="brand-name">bluvoria</h2>
    <p class="tagline">Your business and accounting partner</p>

    <div class="person">
      <p class="person__name">Marcy Elwind</p>
      <p class="person__role">(Principal)</p>
      <p class="person__title">Accountant, Tax Agent</p>
    </div>

    <ul class="contacts">
      <li class="contacts__item">
        <span>0417 683 912</span>
        <svg class="contacts__icon" viewBox="0 0 24 24" aria-label="Phone">
          <rect width="24" height="24" rx="3" fill="var(--blue)"/>
          <path d="M5,10 Q12,4 19,10 L17,12 L15,10 L9,10 L7,12 Z" fill="var(--white)"/>
          <rect x="7" y="12" width="10" height="7" rx="1" fill="var(--white)"/>
        </svg>
      </li>
      <li class="contacts__item">
        <span>Marcy.Elwind@bluvoria.com.au</span>
        <svg class="contacts__icon" viewBox="0 0 24 24" aria-label="Email">
          <rect width="24" height="24" rx="3" fill="var(--blue)"/>
          <rect x="4" y="6" width="16" height="12" fill="none" stroke="var(--white)" stroke-width="1.6"/>
          <path d="M4,6 L12,13 L20,6 M4,18 L10,12 M20,18 L14,12" fill="none" stroke="var(--white)" stroke-width="1.4"/>
        </svg>
      </li>
      <li class="contacts__item">
        <span>www.bluvoria.com.au</span>
        <svg class="contacts__icon" viewBox="0 0 24 24" aria-label="Website">
          <rect width="24" height="24" rx="3" fill="var(--blue)"/>
          <g fill="none" stroke="var(--white)" stroke-width="1.3">
            <circle cx="12" cy="12" r="8"/>
            <ellipse cx="12" cy="12" rx="3.5" ry="8"/>
            <path d="M4,12 H20 M5.5,8 H18.5 M5.5,16 H18.5"/>
          </g>
        </svg>
      </li>
    </ul>

    <p class="location">Kestrel Bay NSW Australia</p>
  </section>

</main>
</body>
</html>
```